RW Framewell Inc Business cards

We need business cards using our existing logo but slightly modified. Right now the logo says RW Loadbearing Masonry. We want to keep the RW part of the design, but replace the Structural Concrete portion with "FRAMEWELL". Please see the attached file.
Ideally this would be a blank template so we can add Different Names, titles, and phone numbers later.
On the one side we want only the logo and on the other side the detail. I'm attaching an example for you to see.
Please reach out with any other questions. Our address and other details will be given out once we find a design we like.

Target Market(s)

Construction Industry

```html
<!DOCTYPE html>
<html lang="en">
<head>
<meta charset="utf-8">
<title>RW Framewell Inc – Business Cards</title>
<link rel="stylesheet" href="https://fonts.googleapis.com/css2?family=Montserrat:wght@700&family=Roboto:wght@400;700&family=Exo+2:wght@600&display=swap">
<style>
  :root {
    --backdrop: #c8c8c8;
    --card: #f7f7f7;
    --brand-blue: #2f62ad;
    --brand-grey: #6b6b6b;
    --text-grey: #5a5a5a;
    --white: #ffffff;
  }
  * { box-sizing: border-box; margin: 0; padding: 0; }
  html, body {
    width: 1200px; height: 852px; overflow: hidden;
    background: var(--backdrop);
    font-family: "Roboto", Arial, sans-serif;
  }
  .sheet {
    position: relative; width: 1200px; height: 852px;
    display: flex; align-items: center; justify-content: center; gap: 50px;
  }
  .card {
    position: relative; width: 525px; height: 300px;
    background: var(--card); border-radius: 22px; overflow: hidden;
    box-shadow: 0 6px 16px rgba(0,0,0,.18);
  }
  /* wordmark: one colour, one weight */
  .wordmark {
    position: absolute; display: flex; flex-direction: column;
    font-family: "Montserrat", Arial, sans-serif; font-weight: 700;
    color: var(--brand-blue); line-height: 1;
  }
  .wordmark__initials { display: flex; align-items: center; gap: 10px; }
  .wordmark__square { width: 16px; height: 16px; background: var(--brand-blue); }
  .wordmark__name { letter-spacing: .28em; }

  /* front */
  .card--front .wordmark { left: 50%; top: 50%; transform: translate(-50%, -55%); }
  .card--front .wordmark__initials { font-size: 88px; }
  .card--front .wordmark__name { font-size: 26px; margin-top: 6px; }
  .front-band { position: absolute; bottom: 0; left: 0; right: 0; height: 10px; display: flex; }
  .front-band__grey { flex: 1; background: var(--brand-grey); }
  .front-band__blue { flex: 1; background: var(--brand-blue); }

  /* back */
  .card--back .wordmark { left: 36px; top: 34px; }
  .card--back .wordmark__initials { font-size: 64px; }
  .card--back .wordmark__name { font-size: 19px; margin-top: 4px; }
  .person { position: absolute; left: 40px; top: 218px; }
  .person__name { font-family: "Exo 2", Arial, sans-serif; font-weight: 600; font-size: 21px; color: var(--brand-blue); }
  .person__title { font-size: 13px; color: var(--text-grey); margin-top: 2px; }
  .contact { position: absolute; left: 290px; top: 120px; list-style: none; font-size: 12.5px; color: var(--text-grey); line-height: 1.45; }
  .contact__item { display: flex; align-items: flex-start; gap: 8px; }
  .contact__icon { width: 12px; height: 12px; margin-top: 3px; flex: none; fill: var(--brand-blue); }
  .contact__item--plain { padding-left: 20px; }
  .back-strip { position: absolute; left: 0; right: 0; bottom: 0; height: 8px; background: var(--brand-grey); }
  .web-tab {
    position: absolute; right: 0; bottom: 0; width: 238px; height: 52px;
    background: var(--brand-blue); border-top-left-radius: 16px;
    display: flex; align-items: center; justify-content: center;
    color: var(--white); font-weight: 700; font-size: 14px;
  }
</style>
</head>
<body>
<main class="sheet">
  <section class="card card--front" aria-label="Card front">
    <div class="wordmark">
      <span class="wordmark__initials"><span class="wordmark__square"></span>RW</span>
      <span class="wordmark__name">FRAMEWELL</span>
    </div>
    <div class="front-band"><span class="front-band__grey"></span><span class="front-band__blue"></span></div>
  </section>

  <section class="card card--back" aria-label="Card back">
    <div class="wordmark">
      <span class="wordmark__initials"><span class="wordmark__square"></span>RW</span>
      <span class="wordmark__name">FRAMEWELL</span>
    </div>
    <ul class="contact">
      <li class="contact__item">
        <svg class="contact__icon" viewBox="0 0 24 24" aria-hidden="true"><path d="M6.6 10.8a15.1 15.1 0 0 0 6.6 6.6l2.2-2.2a1 1 0 0 1 1-.25 11.4 11.4 0 0 0 3.6.57 1 1 0 0 1 1 1V20a1 1 0 0 1-1 1A17 17 0 0 1 3 4a1 1 0 0 1 1-1h3.5a1 1 0 0 1 1 1c0 1.25.2 2.45.57 3.57a1 1 0 0 1-.25 1z"/></svg>
        555-014-2290
      </li>
      <li class="contact__item contact__item--plain">dana@framewell.test</li>
      <li class="contact__item">
        <svg class="contact__icon" viewBox="0 0 24 24" aria-hidden="true"><path d="M2 5h20v14H2z M2 5l10 8 10-8" fill="none" stroke="currentColor"/><path d="M2 5h20v2l-10 7L2 7z"/><path d="M2 8l10 7 10-7v11H2z"/></svg>
        87 Girder Row, Millbrook,<br>Oregon, US 970014
      </li>
    </ul>
    <div class="person">
      <p class="person__name">Dana RW Hollis</p>
      <p class="person__title">Managing Director</p>
    </div>
    <div class="back-strip"></div>
    <div class="web-tab">www.framewell.test</div>
  </section>
</main>
</body>
</html>
```